I want ideas sample designs for my book cover

Hello,

We need a book cover designed in flat and 3D Versions. We would like to have jpg and png for final output and include a copy of the PSD for future revisions.

Here are the basic details:

Title: The Harvest of Quiet Builders
Author: Norman Quillfeather

Dimensions of book:

Was looking at the Pavo website for dimensions. I thought you may want to go on there and look at the different sizes. I used the 6x9” perfect bound US trade size for my book. You will see that this has a spine width of 0.225”, Cover size of 12.48 x 9.25” and spine begins at 6.125”

If you need background info on the author just to get an idea what he does, please check:

http://NormanQuillfeather.example

IMPORTANT: Please see attached document for a more detailed info:

Exact Title Of book
Back Cover
Spine Info
Measurements of book and dimension
Examples of book covers
Norman's photo attached

Thanks,
Darlene

Industry/Entity Type

Life Coaching

Font styles to use
Serif

Requirements
Must have
• Jpg, png and PSD files
• title
• author
• exact dimensions
• front and back cover
• flat and 3d versions

```html
<!DOCTYPE html>
<html lang="en">
<head>
<meta charset="utf-8">
<title>The Harvest of Quiet Builders — Front Cover</title>
<link rel="stylesheet" href="https://fonts.googleapis.com/css2?family=Alfa+Slab+One&family=Josefin+Slab:wght@300;600&family=Questrial&family=Libre+Baskerville:ital,wght@0,700;1,400&display=swap">
<style>
  :root {
    --magenta: #ae1763;
    --magenta-deep: #8e1150;
    --navy: #1f2b45;
    --band-dark: #241641;
    --band-mid: #3a2a68;
    --sky: #bcd6ee;
    --sea: #2f5f86;
    --ink: #111111;
    --white: #ffffff;
    --bulb-tint: #c44a8a;
  }
  html, body { margin: 0; padding: 0; overflow: hidden; background: var(--magenta); }
  .cover {
    position: relative; width: 801px; height: 1200px; overflow: hidden;
    background: var(--magenta);
  }
  .cover > * { position: absolute; }
  .shapes { left: 0; top: 0; width: 801px; height: 1200px; }
  .idea-cluster {
    left: 0; top: 0; width: 290px; height: 420px;
    background: radial-gradient(ellipse at 45% 45%, var(--bulb-tint) 0%, rgba(174,23,99,0) 70%);
    opacity: .55;
  }
  .title { left: 46px; top: 428px; margin: 0; color: var(--white); font-weight: normal; }
  .title span { display: block; }
  .title .lead { font-family: "Josefin Slab", serif; font-weight: 600; font-size: 104px; line-height: 86px; letter-spacing: -1px; }
  .title .middle { font-family: "Josefin Slab", serif; font-weight: 300; font-size: 104px; line-height: 82px; letter-spacing: -1px; }
  .title .last { font-family: "Alfa Slab One", serif; font-size: 68px; line-height: 70px; color: var(--ink); letter-spacing: 1px; }
  .tagline-band {
    left: 0; top: 724px; width: 801px; height: 154px;
    background: radial-gradient(ellipse at 40% 50%, var(--band-mid) 0%, var(--band-dark) 85%);
  }
  .tagline {
    left: 46px; top: 748px; width: 700px; margin: 0;
    font-family: "Questrial", sans-serif; font-size: 21.5px; line-height: 33px; color: var(--white);
  }
  .credit { left: 46px; top: 962px; margin: 0; color: var(--white); font-family: "Questrial", sans-serif; font-size: 30px; line-height: 40px; }
  .credit .prior { display: block; font-family: "Libre Baskerville", serif; font-weight: 700; font-size: 26px; }
  .author { left: 44px; top: 1066px; margin: 0; font-family: "Libre Baskerville", serif; font-style: italic; font-size: 46px; color: var(--ink); }
</style>
</head>
<body>
<main class="cover">
  <svg class="shapes" viewBox="0 0 801 1200" aria-hidden="true">
    <defs>
      <linearGradient id="sceneTone" x1="0" y1="0" x2="0" y2="1">
        <stop offset="0" stop-color="#8fb8e0"/>
        <stop offset=".45" stop-color="var(--sky)"/>
        <stop offset=".55" stop-color="#6f97b8"/>
        <stop offset="1" stop-color="var(--sea)"/>
      </linearGradient>
    </defs>
    <polygon class="corner-mark" points="801,352 716,448 801,552" fill="var(--navy)" stroke="var(--navy)" stroke-width="24" stroke-linejoin="round"/>
    <polygon class="accent-block" points="801,960 716,1048 801,1136" fill="var(--white)" stroke="var(--white)" stroke-width="24" stroke-linejoin="round"/>
    <polygon class="base-wedge" points="576,1040 440,1200 801,1200 801,1240" fill="var(--magenta-deep)" stroke="var(--magenta-deep)" stroke-width="30" stroke-linejoin="round"/>
  </svg>
  <svg class="shapes" viewBox="0 0 801 1200" role="img" aria-label="Photograph of a man in a dark suit seen from behind, looking out over a sunlit ocean">
    <polygon points="380,-20 285,150 596,470 801,300 801,-20" fill="url(#sceneTone)" stroke="url(#sceneTone)" stroke-width="28" stroke-linejoin="round"/>
  </svg>
  <div class="idea-cluster" role="img" aria-label="Line illustration of a cluster of light bulbs rising upward"></div>

  <h1 class="title">
    <span class="lead">the harvest</span>
    <span class="middle">of quiet</span>
    <span class="last">BUILDERS</span>
  </h1>

  <div class="tagline-band"></div>
  <p class="tagline">How this ancient wisdom is helping billionaires, industry icons and entrepreneurs to be better leaders, increase impact and leave a legacy.</p>

  <p class="credit">From the Best Selling Author of <span class="prior">“ENVISION”</span></p>
  <p class="author">Norman Quillfeather</p>
</main>
</body>
</html>
```